Presentation Folder, for Cancer Awareness, VERY COLORFULL AND MODERN

This will be a standard size folder that will hold standard 8 1/2 x 11 papers with a business card slot on the flap, this is a very easy project with very little text and the design for the back page is already done so all you really have to do is make a very nice colorful front cover, you will see my attachments are labeled and I gave you alot of instructions, this should be a very fast easy project
Updates

Reason: there has not been enough quality designs, sorry

Target Market(s)

Our Target Market is Dr's that Deal with Cancer patients

Industry/Entity Type

Healthcare

Font styles to use
Serif

Colors

Designer to choose colors to be used in the design.

Requirements
Must have
• Project must be tasteful and look professional with the ribbons as the main focal point in the center of folder the folder should be a nice gray color to accent the color of the ribbons , the back page needs no design it is the" Sorvane Test" in the attachments I sent
Nice to have
• I would like the ribbons displayed in a row, I included a logo sample layout
• a picture on the front of the folder under the words Hereditary Cancer Screening - Then under that put the words - The Power of Knowledge - then add the picture I labeled Great Picture in the attachments

```html
<!DOCTYPE html>
<html lang="en">
<head>
<meta charset="utf-8">
<title>Hereditary Cancer Screening Folder</title>
<link rel="stylesheet" href="https://fonts.googleapis.com/css2?family=Montserrat:wght@700;800&family=Raleway:wght@300;400&family=Lato:wght@400;700&display=swap">
<style>
  :root {
    --backdrop: #e4e4e4;
    --sheet: #f7f7f7;
    --red: #d6201f;
    --title-red: #e0342c;
    --ink: #4a4a4a;
    --muted: #8a8a8a;
    --row-alt: #e6e6e6;
    --head-dark: #5a5a5a;
    --lynch: #f6c12e;
    --peutz: #b5cf3a;
    --lifra: #3cb04e;
    --cowden: #1a8fd6;
    --hdgc: #6b6b66;
  }
  * { box-sizing: border-box; margin: 0; padding: 0; }
  html, body { width: 1200px; height: 1000px; overflow: hidden; }
  body {
    background: var(--backdrop);
    font-family: "Lato", sans-serif;
    position: relative;
  }
  .panel {
    position: absolute;
    top: 110px;
    width: 500px;
    height: 780px;
    background: var(--sheet);
    box-shadow: 0 10px 30px rgba(0,0,0,0.15);
  }
  .front-cover { left: 60px; text-align: center; }
  .back-page { left: 640px; padding: 54px 40px 30px; }

  .brand { display: flex; flex-direction: column; align-items: center; gap: 14px; }
  .brand-dot { width: 44px; height: 44px; border-radius: 50%; background: var(--red); }
  .brand-name {
    font-family: "Raleway", sans-serif; font-weight: 300;
    letter-spacing: 5px; color: var(--red); font-size: 26px;
  }
  .front-cover .brand { margin-top: 70px; }

  .headline {
    margin-top: 58px;
    font-family: "Montserrat", sans-serif; font-weight: 800;
    color: var(--red); font-size: 24px; letter-spacing: -0.3px;
  }
  .ribbon-art { display: block; margin: 22px auto 0; }
  .tagline {
    margin-top: 26px;
    font-family: "Raleway", sans-serif; font-weight: 300;
    color: var(--muted); font-size: 25px; letter-spacing: 4px;
  }

  .menu-head { display: flex; justify-content: space-between; align-items: flex-start; margin-bottom: 20px; }
  .menu-title { font-family: "Raleway", sans-serif; font-weight: 400; color: var(--title-red); font-size: 21px; }
  .menu-title sup { font-size: 9px; }
  .menu-meta { text-align: right; font-size: 9px; color: var(--muted); letter-spacing: 1px; line-height: 1.4; }

  .gene-table { width: 100%; border-collapse: collapse; font-size: 7.5px; }
  .gene-table td, .gene-table th { padding: 0 6px; height: 12.4px; text-align: left; }
  .gene-table tr:nth-child(even) td { background: var(--row-alt); }
  .gene-table td.gene { color: var(--red); font-weight: 700; width: 42%; }
  .gene-table td.organ { color: var(--ink); }
  .gene-table th { font-size: 9px; color: #fff; font-weight: 700; height: 14px; }
  .gene-table th.col-gene { background: var(--red); }
  .gene-table th.col-organ { background: var(--head-dark); }
  .gene-table tr.section td { color: #fff; font-weight: 700; font-size: 8.5px; height: 13px; }
  .section.lynch td { background: var(--lynch) !important; }
  .section.peutz td { background: var(--peutz) !important; }
  .section.lifra td { background: var(--lifra) !important; }
  .section.cowden td { background: var(--cowden) !important; }
  .section.hdgc td { background: var(--hdgc) !important; }

  .back-footer {
    position: absolute; left: 40px; right: 40px; bottom: 36px;
    display: flex; justify-content: space-between; align-items: center;
  }
  .back-footer .brand { flex-direction: row; gap: 8px; }
  .back-footer .brand-dot { width: 18px; height: 18px; }
  .back-footer .brand-name { font-size: 14px; letter-spacing: 3px; }
  .contact { font-size: 6.5px; color: var(--muted); line-height: 1.6; text-align: left; }
</style>
</head>
<body>

<section class="panel front-cover">
  <div class="brand">
    <span class="brand-dot"></span>
    <span class="brand-name">CELLVARO LABS</span>
  </div>
  <h1 class="headline">HEREDITARY CANCER SCREENING</h1>
  <svg class="ribbon-art" width="340" height="420" role="img" aria-label="Two rows of colourful cancer awareness ribbons">
    <defs>
      <linearGradient id="ribbonTones" x1="0" y1="0" x2="1" y2="1">
        <stop offset="0" stop-color="#f59a9a"/>
        <stop offset="0.2" stop-color="#8cc63f"/>
        <stop offset="0.35" stop-color="#1f7fd6"/>
        <stop offset="0.5" stop-color="#6fc6e8"/>
        <stop offset="0.65" stop-color="#f2a8c8"/>
        <stop offset="0.8" stop-color="#a35ad8"/>
        <stop offset="1" stop-color="#8a4a14"/>
      </linearGradient>
    </defs>
    <rect width="340" height="420" rx="6" fill="url(#ribbonTones)" opacity="0.85"/>
  </svg>
  <p class="tagline">The Power of Knowledge</p>
</section>

<section class="panel back-page">
  <header class="menu-head">
    <h2 class="menu-title">SORVANE<sup>™</sup> Test Menu</h2>
    <div class="menu-meta">CLIA# 00D0000000<br>CELLVAROLABS.COM</div>
  </header>

  <table class="gene-table">
    <tr><th class="col-gene">GENE</th><th class="col-organ">CANCER-ASSOCIATED ORGAN/SYSTEMS</th></tr>
    <tr><td class="gene">APC</td><td class="organ">Colon</td></tr>
    <tr><td class="gene">ATM</td><td class="organ">Breast/Pancreatic/Brain</td></tr>
    <tr><td class="gene">BARD1</td><td class="organ">Breast/Ovarian</td></tr>
    <tr><td class="gene">BMPR1A</td><td class="organ">Colon</td></tr>
    <tr><td class="gene">BRCA1</td><td class="organ">Breast/Ovarian/Prostate</td></tr>
    <tr><td class="gene">BRCA2</td><td class="organ">Breast/Ovarian/Prostate</td></tr>
    <tr><td class="gene">BRIP1</td><td class="organ">Breast/Ovarian</td></tr>
    <tr><td class="gene">CDK4</td><td class="organ">Melanoma</td></tr>
    <tr><td class="gene">P16 (CDKN2A)</td><td class="organ">Melanoma/Breast/Pancreatic/Squamous</td></tr>
    <tr><td class="gene">FANCC</td><td class="organ">Blood</td></tr>
    <tr><td class="gene">MEN1</td><td class="organ">Thyroid/Parathyroid</td></tr>
    <tr><td class="gene">MET</td><td class="organ">Renal/Hepatic</td></tr>
    <tr><td class="gene">MRE11A</td><td class="organ">Ovarian/Breast</td></tr>
    <tr><td class="gene">NBN</td><td class="organ">Breast/Ovarian/Prostate/Melanoma</td></tr>
    <tr><td class="gene">NF1</td><td class="organ">Blood</td></tr>
    <tr><td class="gene">NTRK1</td><td class="organ">Thyroid/Parathyroid</td></tr>
    <tr><td class="gene">PALB2</td><td class="organ">Breast/Ovarian/Pancreatic</td></tr>
    <tr><td class="gene">PTCH1</td><td class="organ">Melanoma/Brain/Breast/Colon</td></tr>
    <tr><td class="gene">RAD50</td><td class="organ">Breast/Ovarian</td></tr>
    <tr><td class="gene">RAD51C</td><td class="organ">Ovarian/Breast</td></tr>
    <tr><td class="gene">RAD51D</td><td class="organ">Ovarian/Breast</td></tr>
    <tr><td class="gene">RET</td><td class="organ">Lung/Thyroid/Parathyroid</td></tr>
    <tr><td class="gene">SMAD4</td><td class="organ">Colon/Pancreas</td></tr>
    <tr class="section lynch"><td colspan="2">LYNCH SYNDROME GENES</td></tr>
    <tr><td class="gene">MLH1</td><td class="organ">Colorectal/Ovarian</td></tr>
    <tr><td class="gene">MSH2</td><td class="organ">Colorectal/Ovarian</td></tr>
    <tr><td class="gene">MSH6</td><td class="organ">Colorectal/Ovarian</td></tr>
    <tr><td class="gene">PMS2</td><td class="organ">Colorectal/Ovarian</td></tr>
    <tr><td class="gene">EPCAM</td><td class="organ">Colorectal</td></tr>
    <tr class="section peutz"><td colspan="2">PEUTZ-JEGHERS SYNDROME GENE</td></tr>
    <tr><td class="gene">STK11</td><td class="organ">Breast/Ovarian/Melanoma/Colorectal/Lung</td></tr>
    <tr class="section lifra"><td colspan="2">LI-FRAUMENI SYNDROME GENE</td></tr>
    <tr><td class="gene">CHEK2</td><td class="organ">Breast/Ovarian/Prostate</td></tr>
    <tr><td class="gene">P53</td><td class="organ">Breast/Bladder/Ovarian/Squamous</td></tr>
    <tr class="section cowden"><td colspan="2">COWDEN SYNDROME GENE</td></tr>
    <tr><td class="gene">PTEN</td><td class="organ">Endometrium/Breast/Prostate/Lung</td></tr>
    <tr class="section hdgc"><td colspan="2">HEREDITARY DIFFUSE GASTRIC CANCER SYNDROME GENE</td></tr>
    <tr><td class="gene">CDH1</td><td class="organ">Breast/Gastric/Ovarian/Prostate</td></tr>
    <tr><td class="gene">VHL</td><td class="organ">Renal</td></tr>
  </table>

  <footer class="back-footer">
    <div class="brand">
      <span class="brand-dot"></span>
      <span class="brand-name">CELLVARO LABS</span>
    </div>
    <address class="contact">
      1400 Harbor Point Way | Suite B | Dayton, OH 45402<br>
      Tel 555.010.2200 | Fax 555.010.2201 | info@cellvarolabs.com
    </address>
  </footer>
</section>

</body>
</html>
```